Web site for small printshop

I am looking for a website for small printshop in Iceland, mainly serving university students and artist.

We print posters, flyers, business cards and more.

In addition to our current website, I would like to include design tool, (fx. www.quarvelpad.example, www.trindomap.example or something similar) jobs upload, shopping chart.
Updates

Great work, I am really amazed of the quality of work i am seeing here.

Really way beyond my expectation

GOOD JOB - all of you ! 

Hi all.

The designs submitted have been great, way better than expected.
I really did not expect this level of quality.

Some have been asking me for feedback on their designs, and I will try 
to send some feedback here, without spoiling your creativity.

Likes:
- when the colors of my logo is used in menus, buttons etc.
- simple, not to crowded look.

Dislikes.
- Dark and heavy design
- Lot of text and buttons (crowded look)

Extra info.
- top line (before menus) will contain: Tel - email - language
- menu line will have 5 categories: Home - service - submission of works - FAQ - about us
- 3 large buttons:  Job submit - Job design - ask for offer

LOVE YOUR WORK - great designs so far :)

Target Market(s)

University Students, Artists. Age group 20-30

Industry/Entity Type

University

Requirements
Must have
• The website must be easy to use, clean looking.

```html
<!DOCTYPE html>
<html lang="en">
<head>
<meta charset="utf-8">
<title>Grafvik Print – Printing Solutions</title>
<link href="https://fonts.googleapis.com/css2?family=Ubuntu:wght@300;400;500;700&display=swap" rel="stylesheet">
<style>
  :root {
    --red: #e7332f;
    --red-light: #f25d57;
    --red-dark: #e12a26;
    --green: #23822b;
    --green-dark: #145a1b;
    --yellow: #f8d21a;
    --ink: #2b2b2b;
    --muted: #8a8a8a;
    --line: #e8e8e8;
    --footer: #2f2f2f;
  }
  * { box-sizing: border-box; margin: 0; padding: 0; }
  html, body { width: 834px; height: 1200px; overflow: hidden; background: #fff; }
  body { position: relative; font-family: "Ubuntu", sans-serif; color: var(--ink); }
  .abs { position: absolute; }

  /* header */
  .brand { left: 84px; top: 14px; display: flex; align-items: center; gap: 10px; }
  .brand-mark { width: 32px; height: 42px; background: var(--red); }
  .brand-name { font-size: 28px; font-weight: 500; color: #222; letter-spacing: 0.5px; }
  .call { right: 84px; top: 8px; font-size: 10px; color: #666; }
  .call strong { font-size: 13px; font-weight: 400; color: #444; margin-left: 3px; }
  .main-nav { right: 84px; top: 38px; display: flex; font-size: 12px; }
  .main-nav a { color: #222; text-decoration: none; padding: 0 8px; border-left: 1px solid #ccc; line-height: 12px; }
  .main-nav a:first-child { border-left: none; }
  .main-nav a:last-child { padding-right: 0; }

  /* hero */
  .hero { left: 0; top: 76px; width: 834px; height: 271px; background: linear-gradient(180deg, var(--red-light), var(--red-dark)); }
  .hero-kicker { left: 86px; top: 49px; font-size: 19px; font-weight: 300; color: #fff; }
  .hero-title { left: 86px; top: 72px; font-size: 32px; font-weight: 400; color: #fff; }
  .hero-text { left: 89px; top: 111px; width: 260px; font-size: 9.5px; line-height: 16.5px; color: #fff; font-weight: 300; }
  .btn { left: 87px; top: 166px; width: 106px; height: 26px; background: var(--yellow); color: #222; font-size: 11px; display: flex; align-items: center; justify-content: center; border-radius: 2px; }
  .dots { left: 89px; top: 211px; display: flex; gap: 2px; }
  .dots span { width: 8px; height: 8px; border-radius: 50%; background: #c81f1c; }
  .dots span:first-child { background: #fff; }
  .hero-visual { left: 354px; top: 46px; width: 397px; height: 164px; border: 6px solid #eee; border-radius: 3px; background: linear-gradient(120deg, #3a3a3a 0%, #8a8a8a 22%, #f18a1c 35%, #f57c14 60%, #d1221f 75%, #b81b1b 100%); box-shadow: 0 2px 6px rgba(0,0,0,0.25); }

  /* steps */
  .step { width: 216px; height: 121px; top: 366px; background: linear-gradient(#fff, #f7f7f7); border: 1px solid #e0e0e0; box-shadow: 0 1px 3px rgba(0,0,0,0.12); }
  .step-tab { position: absolute; left: -8px; top: -3px; width: 105px; height: 32px; background: linear-gradient(var(--green), var(--green-dark)); color: #fff; font-size: 16px; padding: 6px 0 0 27px; border-radius: 0 18px 18px 0; }
  .step-title { position: absolute; left: 18px; top: 41px; font-size: 16px; color: var(--green); font-weight: 500; }
  .step-text { position: absolute; left: 19px; top: 64px; width: 118px; font-size: 7.5px; line-height: 11.5px; color: var(--muted); font-weight: 300; }
  .step-icon { position: absolute; left: 140px; top: 42px; width: 60px; height: 56px; }

  .rule { left: 80px; width: 674px; height: 1px; background: var(--line); }

  /* features */
  .feature h2 { font-size: 18px; font-weight: 400; color: #222; margin-bottom: 8px; }
  .feature p { font-size: 9px; line-height: 16px; color: var(--muted); font-weight: 300; }
  .art { border-radius: 4px; }

  /* partners */
  .partners { left: 122px; top: 1008px; width: 590px; height: 36px; display: flex; justify-content: space-between; align-items: center; }
  .partners span { background: #b9b9b9; border-radius: 3px; }

  /* footer */
  .footer { left: 0; top: 1096px; width: 834px; height: 104px; background: linear-gradient(#3a3a3a, var(--footer)); }
  .foot-nav { left: 86px; top: 28px; font-size: 10px; color: #fff; }
  .foot-nav span { color: #aaa; margin: 0 5px; }
  .copy { left: 86px; top: 50px; font-size: 8.5px; color: #999; font-weight: 300; }
  .social { right: 88px; top: 28px; display: flex; gap: 6px; }
  .social span { width: 18px; height: 18px; border-radius: 2px; background: #6d7b8c; }
</style>
</head>
<body>

<header>
  <div class="abs brand"><span class="brand-mark"></span><span class="brand-name">GRAFVIK PRINT</span></div>
  <div class="abs call">CALL US <strong>555-0142</strong></div>
  <nav class="abs main-nav"><a>Home</a><a>About</a><a>Features</a><a>Services</a><a>How it Works</a><a>Contact</a></nav>
</header>

<section class="abs hero">
  <div class="abs hero-kicker">Mauris vel lacus vitae felis</div>
  <h1 class="abs hero-title">Printing Solutions..</h1>
  <p class="abs hero-text">Ut nisi erat, fermentum vel, congue id, euismod in, elit. Fusce ultricies, orci ac feugiat suscipit, leo massa sodales velit, et scelerisque mi tortor at ipsum.</p>
  <div class="abs btn">Browse Image</div>
  <div class="abs dots"><span></span><span></span><span></span><span></span></div>
  <div class="abs hero-visual" role="img" aria-label="Printed business cards and design samples"></div>
</section>

<section class="steps">
  <div class="abs step" style="left:78px">
    <div class="step-tab">Step 1</div>
    <div class="step-title">Creating</div>
    <p class="step-text">Vivamus porttitor, g, purus nisi eleifend libero, a tempus libero lectus feugiat felis</p>
    <svg class="step-icon" viewBox="0 0 60 56"><path d="M10 8 L52 14 L44 44 Q40 54 28 50 Q18 46 6 40 Q16 40 22 36 Z" fill="none" stroke="var(--red)" stroke-width="5" stroke-linejoin="round"/></svg>
  </div>
  <div class="abs step" style="left:309px">
    <div class="step-tab">Step 2</div>
    <div class="step-title">Uploading</div>
    <p class="step-text">Vivamus porttitor, g, purus nisi eleifend libero, a tempus libero lectus feugiat felis</p>
    <svg class="step-icon" viewBox="0 0 60 56"><rect x="8" y="6" width="46" height="46" rx="6" fill="none" stroke="var(--red)" stroke-width="5"/><path d="M31 14 L20 26 H27 V36 H35 V26 H42 Z" fill="var(--red)"/><path d="M18 36 V42 H44 V36" fill="none" stroke="var(--red)" stroke-width="4"/></svg>
  </div>
  <div class="abs step" style="left:539px">
    <div class="step-tab">Step 3</div>
    <div class="step-title">Get Printed</div>
    <p class="step-text">Vivamus porttitor, g, purus nisi eleifend libero, a tempus libero lectus feugiat felis</p>
    <svg class="step-icon" viewBox="0 0 60 56"><rect x="15" y="2" width="30" height="12" fill="var(--red)"/><rect x="2" y="17" width="56" height="22" rx="5" fill="var(--red)"/><rect x="15" y="32" width="30" height="20" fill="var(--red)" stroke="#fff" stroke-width="3"/></svg>
  </div>
</section>

<div class="abs rule" style="top:526px"></div>

<section class="abs feature" style="left:84px; top:561px; width:430px">
  <h2>Fully Customizable</h2>
  <p>Vivamus porttitor, g, purus nisi eleifend libero, a tempus libero lectus feugiat felis. Morbi diam mauris, viverra in, gravida eu, mattis in, ante. Morbi eget arcu. Morbi porta, libero id ullamcorper nonummy, nibh ligula pulvinar metus, eget consectetuer augue nisi quis lacus. Ut ac mi quis lacus mollis aliquam. Curabitur iaculis tempus eros. Curabitur vel mi sit amet magna malesuada ultrices.</p>
</section>
<div class="abs art" style="left:540px; top:552px; width:184px; height:124px; background:linear-gradient(110deg,#666,#e8d62a 35%,#d33ca4 55%,#2a9fd8 80%,#1d6fb4)" role="img" aria-label="Stack of colourful print proof sheets"></div>

<div class="abs art" style="left:116px; top:680px; width:114px; height:118px; background:linear-gradient(135deg,#5ab6e0,#f0e8f0 45%,#e2e2e2)" role="img" aria-label="Printed report document"></div>
<section class="abs feature" style="left:332px; top:703px; width:420px">
  <h2>Extensibile via Modules</h2>
  <p>Vivamus porttitor, g, purus nisi eleifend libero, a tempus libero lectus feugiat felis. Morbi diam mauris, viverra in, gravida eu, mattis in, ante. Morbi eget arcu. Morbi porta, libero id ullamcorper nonummy, nibh ligula pulvinar metus, eget consectetuer augue nisi quis lacus. Ut ac mi quis lacus mollis aliquam. Curabitur iaculis tempus eros. Curabitur vel mi sit amet magna malesuada ultrices.</p>
</section>

<section class="abs feature" style="left:83px; top:835px; width:430px">
  <h2>Generate Full Vector</h2>
  <p>Vivamus porttitor, g, purus nisi eleifend libero, a tempus libero lectus feugiat felis. Morbi diam mauris, viverra in, gravida eu, mattis in, ante. Morbi eget arcu. Morbi porta, libero id ullamcorper nonummy, nibh ligula pulvinar metus, eget consectetuer augue nisi quis lacus. Ut ac mi quis lacus mollis aliquam. Curabitur iaculis tempus eros. Curabitur vel mi sit amet magna malesuada ultrices.</p>
</section>
<div class="abs art" style="left:554px; top:814px; width:170px; height:140px; background:linear-gradient(135deg,#e9e9e9,#f2c23a 30%,#e2473a 55%,#3f7fc4 80%,#dcdcdc)" role="img" aria-label="Fanned colour swatch guide"></div>

<div class="abs rule" style="top:974px"></div>

<div class="abs partners" aria-label="Partners">
  <span style="width:28px;height:36px"></span>
  <span style="width:80px;height:22px"></span>
  <span style="width:64px;height:22px"></span>
  <span style="width:58px;height:20px"></span>
  <span style="width:66px;height:16px"></span>
  <span style="width:22px;height:12px"></span>
  <span style="width:64px;height:28px"></span>
  <span style="width:54px;height:28px"></span>
</div>

<footer class="abs footer">
  <div class="abs foot-nav">Home<span>/</span>About<span>/</span>Features<span>/</span>Services<span>/</span>How it Works<span>/</span>Contact</div>
  <div class="abs copy">© 2013 Company Name. &nbsp;All right reserved. &nbsp;Term of Use</div>
  <div class="abs social" aria-label="Social links"><span></span><span></span><span></span><span></span></div>
</footer>

</body>
</html>
```